Business Card Design

New business card design

Target Market(s)

Residential & Commercial Property Managers

Industry/Entity Type

Plumbing Services

Contact Information for Business Card

Name - Rowan Keddle, title - Director, Phone Number - 0431 286 517, email - rowan@tbk-plumbing.com.au, Company ABN - 73 215 904 386,

Font styles to use
Sans Serif

Colors
0054AA
0677BA
7BADD7
CADEEF
E8F1F8

```html
<!DOCTYPE html>
<html lang="en">
<head>
<meta charset="utf-8">
<title>tbk plumbing services – business card</title>
<link rel="stylesheet" href="https://fonts.googleapis.com/css2?family=Arimo:wght@400&display=swap">
<style>
  :root {
    --backdrop: #9b9b9b;
    --card-white: #f6f6f5;
    --card-dark: #1b2026;
    --ink: #2b3239;
    --ink-soft: #6f6a66;
    --accent: #0677ba;
    --accent-deep: #0054aa;
    --on-dark: #e8f1f8;
    --rule: #b9b9b9;
  }
  * { margin: 0; padding: 0; box-sizing: border-box; }
  html, body { width: 1200px; height: 1050px; overflow: hidden; }
  body {
    background: var(--backdrop);
    font-family: "Arimo", Arial, sans-serif;
    position: relative;
  }
  .card {
    position: absolute;
    left: 320px;
    width: 560px;
    height: 320px;
    border-radius: 22px;
  }
  .card--front { top: 160px; background: var(--card-white); }
  .card--back { top: 570px; background: var(--card-dark); }

  .brand {
    position: absolute;
    top: 52px;
    left: 0;
    width: 100%;
    text-align: center;
  }
  .brand__name {
    font-size: 96px;
    line-height: 1;
    color: var(--ink);
    letter-spacing: 4px;
  }
  .brand__tagline {
    margin-top: 14px;
    font-size: 15px;
    color: var(--ink-soft);
    letter-spacing: 13px;
    padding-left: 13px;
  }

  .contact {
    position: absolute;
    top: 222px;
    left: 0;
    width: 100%;
    display: flex;
    justify-content: center;
    align-items: center;
  }
  .contact__person {
    padding-right: 16px;
    text-align: right;
    font-size: 14px;
    line-height: 21px;
  }
  .contact__name { color: var(--ink); }
  .contact__role { color: var(--accent); }
  .contact__divider {
    width: 1px;
    height: 66px;
    background: var(--rule);
  }
  .contact__details {
    padding-left: 16px;
    font-size: 14px;
    color: var(--ink);
    line-height: 21px;
  }
  .contact__row { display: flex; align-items: center; gap: 8px; }
  .contact__icon { width: 12px; height: 12px; fill: var(--ink); flex: none; }

  .back__mark {
    position: absolute;
    top: 70px;
    left: 50%;
    width: 130px;
    height: 130px;
    margin-left: -65px;
    border-radius: 50%;
    background: var(--accent);
  }
  .back__web {
    position: absolute;
    top: 240px;
    width: 100%;
    text-align: center;
    color: var(--on-dark);
    font-size: 15px;
    letter-spacing: 0.5px;
  }
</style>
</head>
<body>
  <section class="card card--front">
    <div class="brand">
      <div class="brand__name">tbk</div>
      <div class="brand__tagline">plumbing services</div>
    </div>
    <div class="contact">
      <div class="contact__person">
        <div class="contact__name">Rowan Keddle</div>
        <div class="contact__role">Director</div>
      </div>
      <div class="contact__divider"></div>
      <div class="contact__details">
        <div class="contact__row">ABN - 73 215 904 386</div>
        <div class="contact__row">
          <svg class="contact__icon" viewBox="0 0 24 24" aria-hidden="true"><path d="M6.6 10.8a15 15 0 0 0 6.6 6.6l2.2-2.2a1 1 0 0 1 1-.25 11.4 11.4 0 0 0 3.6.57 1 1 0 0 1 1 1V20a1 1 0 0 1-1 1A17 17 0 0 1 3 4a1 1 0 0 1 1-1h3.5a1 1 0 0 1 1 1c0 1.25.2 2.45.57 3.57a1 1 0 0 1-.25 1z"/></svg>
          0431 286 517
        </div>
        <div class="contact__row">
          <svg class="contact__icon" viewBox="0 0 24 24" aria-hidden="true"><path d="M2 5h20v14H2z M4 7v.4l8 5.2 8-5.2V7z" fill-rule="evenodd"/></svg>
          rowan@tbk-plumbing.com.au
        </div>
      </div>
    </div>
  </section>

  <section class="card card--back">
    <div class="back__mark"></div>
    <div class="back__web">www.tbk-plumbing.com</div>
  </section>
</body>
</html>
```